Wordpress Design for a Digital Management Consulting Business

I need a simple Wordpress Design and someone to set it up for a new boutique management consulting business called Quillon Advisory that specialises in providing strategic advice to help grow digital businesses. It covers business strategy, marketing strategy, digital strategy, web product development, marketing campaigns, social, search, etc. From strategy to implementation.

URL is: quillonadvisory.com.au

My professional background is here: au.linkedin.com/in/hollyprenwick

Competitors: other boutique digital/marketing management consulting businesses in Australia

The logos, colours and fonts are attached.

I would like the site to convey a business that is Smart/intelligent, Contemporary, Progressive, Digital, Energetic, Friendly.

The objective of the site is to educate visitors about what Quillon Advisory does and encourage them to contact me for more information. It will be very light on content.

Target Market(s)

CEOs/Managing Directors, General Managers, Marketing Directors

Industry/Entity Type

Management Consulting

Font styles to use
Sans Serif

Colors
e34197
5c5c5c
000000

Requirements
Must have
• Site design requirements:
• Choose an appropriate Wordpress template, set it up for me and let me be able to edit it ongoing.
• It should use lots of images - these can be inspirational and not necessarily tied directly to the work
• Pink should feature, but not be the dominant colour.
• Site structure should be:
• 1. Home page - image led with horizontal navigation. Text beneath and images to describe the services.
• 2. About page - with space to write text and insert a picture of the Director
• 3. Services - with space to highlight services either as a list or graphically with text
• 4. Contact page - with space to write text and add email links, etc.
• Should have horizontal navigation
• It should have the flexibility to add another page
Nice to have
• Use the tree icon somehow in the design - consider in the background enlarged
• Use pink, grey, black from logo. Can introduce another complimentary colour if necessary.
• Can introduce another complimentary font to go with the logo font.
Should not have
• Use cliched business images and icons, eg. business suits, hand shakes, business men, business ties.

```html
<!DOCTYPE html>
<html lang="en">
<head>
<meta charset="utf-8">
<title>Quillon Advisory</title>
<link href="https://fonts.googleapis.com/css2?family=Open+Sans:wght@400;600;700;800&display=swap" rel="stylesheet">
<style>
:root{
  --pink:#e34197;
  --grey:#5c5c5c;
  --black:#000;
  --light:#f3f3f3;
  --dark:#2b2b2b;
  --darker:#1f1f1f;
  --white:#fff;
}
*{margin:0;padding:0;box-sizing:border-box}
html,body{width:1200px;height:2912px;overflow:hidden}
body{font-family:"Open Sans",Arial,sans-serif;color:var(--grey);background:var(--white);position:relative}
.page{position:relative;width:1200px;height:2912px}
p{font-size:13px;line-height:20px}
.site-header{height:112px;display:flex;align-items:center;justify-content:space-between;padding:0 70px;border-bottom:1px solid #e6e6e6}
.brand{display:flex;align-items:center;gap:12px;color:var(--pink);font-weight:700;font-size:28px;letter-spacing:.5px}
.brand-mark{width:30px;height:30px;background:var(--pink)}
.main-nav{display:flex;height:112px}
.main-nav a{display:flex;align-items:center;padding:0 24px;font-size:13px;font-weight:600;color:var(--grey);text-decoration:none;text-transform:uppercase}
.main-nav a.active{background:var(--pink);color:var(--white)}
.hero{position:relative;height:520px;background:linear-gradient(90deg,#6f7682 0%,#a9b1bb 40%,#cfd5dc 70%,#9aa3ad 100%);overflow:hidden}
.hero-photo{position:absolute;right:120px;top:0;width:520px;height:520px;background:linear-gradient(180deg,#b9c0c8 0%,#52596a 100%)}
.hero-copy{position:absolute;left:70px;top:150px;width:440px;color:var(--white)}
.hero-copy h1{font-size:58px;font-weight:800;color:var(--pink);line-height:62px}
.hero-copy h2{font-size:28px;font-weight:700;line-height:34px;text-transform:uppercase}
.hero-copy p{margin:14px 0 22px;color:#eef0f3}
.btn{display:inline-block;background:var(--darker);color:var(--white);font-size:15px;font-weight:600;padding:10px 22px}
.welcome{text-align:center;padding-top:44px;height:152px}
.welcome h2{font-size:26px;font-weight:600;color:#333;line-height:36px;text-transform:uppercase}
.welcome h2 span{color:var(--pink)}
.cards{display:flex;justify-content:center;gap:48px;height:400px}
.card{width:320px;height:372px;background:var(--light);padding:12px}
.card-img{height:130px}
.card h3{font-size:24px;font-weight:600;color:#333;margin:16px 0 8px}
.card p{font-size:12px;line-height:18px}
.what-we-do{background:var(--pink);color:var(--white);height:650px;padding:30px 70px 0;text-align:center}
.section-title{font-size:30px;font-weight:700;text-transform:uppercase}
.what-we-do .intro{margin:10px auto 24px;width:1000px}
.approach-row{display:flex;justify-content:space-between;padding:0 30px}
.approach{width:300px}
.circle{width:180px;height:180px;border-radius:50%;margin:0 auto 20px;border:5px solid rgba(255,255,255,.6)}
.approach h3{font-size:26px;font-weight:600;line-height:30px;margin-bottom:10px}
.approach p{font-size:12px;line-height:18px}
.about{height:270px;padding:32px 70px 0;display:flex;gap:50px}
.about .text{width:770px}
.about .section-title{color:#333;margin-bottom:10px}
.about p{margin-bottom:10px;font-size:12px;line-height:18px}
.about-img{width:250px;height:200px;background:radial-gradient(circle at 45% 45%,#c8b0e6,#7a4fb5 55%,#d9d2e8 100%)}
.director{height:420px;padding:16px 70px 0;display:flex;gap:50px;border-top:1px solid #eee}
.director-photo{width:300px;height:380px;background:linear-gradient(180deg,#d9c9b8,#a98a6f)}
.director h2{font-size:32px;font-weight:700;color:var(--pink);text-transform:uppercase;margin:10px 0 14px}
.director p{font-size:12px;line-height:18px;margin-bottom:12px;width:730px}
.site-footer{background:var(--dark);height:312px;color:#ddd;display:flex;padding:30px 70px 0;gap:40px}
.site-footer h4{font-size:24px;font-weight:600;color:var(--white);margin-bottom:16px}
.foot-col ul{list-style:none;font-size:13px;line-height:24px}
.foot-col li::before{content:"›";color:var(--pink);margin-right:8px}
.col-links{width:220px}.col-services{width:230px}.col-social{width:230px}
.socials{display:flex;gap:10px;margin-bottom:30px}
.socials span{width:30px;height:30px;border-radius:50%;background:#555}
.news-field{display:flex}
.news-field span{background:var(--white);color:#999;font-size:12px;padding:8px 10px;width:150px}
.news-field b{background:var(--pink);color:var(--white);font-size:12px;padding:8px 10px}
.contact-line{display:flex;gap:12px;font-size:13px;line-height:18px;margin-bottom:16px;align-items:flex-start}
.contact-line svg{flex:none}
.contact-line strong{color:var(--white)}
.phone{font-size:20px;font-weight:600;color:var(--white)}
.bottom-bar{background:var(--pink);color:var(--white);height:40px;font-size:12px;text-align:center;line-height:40px}
</style>
</head>
<body>
<div class="page">
  <header class="site-header">
    <div class="brand"><span class="brand-mark"></span>Quillon Advisory</div>
    <nav class="main-nav">
      <a class="active" href="#">Home</a><a href="#">Service</a><a href="#">Projects</a><a href="#">News</a><a href="#">Contacts</a>
    </nav>
  </header>

  <section class="hero">
    <div class="hero-photo" role="img" aria-label="Professional standing in front of a city skyline"></div>
    <div class="hero-copy">
      <h1>ACHIEVE</h1>
      <h2>Your goals and<br>long-term success</h2>
      <p>Clear strategy and practical delivery to help your digital business grow with confidence every step of the way.</p>
      <span class="btn">Click Here</span>
    </div>
  </section>

  <section class="welcome">
    <h2>Welcome to <span>Quillon Advisory!</span> We can be your guide<br>to the world of investments</h2>
  </section>

  <section class="cards">
    <article class="card">
      <div class="card-img" role="img" aria-label="Hands working on a tablet with charts" style="background:linear-gradient(135deg,#cfe0ee,#6d8fb0)"></div>
      <h3>Digital Strategy</h3>
      <p>We shape a digital plan that fits your goals, your market and your team, turning ideas into clear steps that deliver measurable growth for your business.</p>
    </article>
    <article class="card">
      <div class="card-img" role="img" aria-label="Team reviewing marketing reports at a desk" style="background:linear-gradient(135deg,#eef1f4,#9aa6b3)"></div>
      <h3>Marketing Strategy</h3>
      <p>From positioning to campaigns, we help you reach the right people with the right message, across social, search and every channel that matters most.</p>
    </article>
    <article class="card">
      <div class="card-img" role="img" aria-label="Modern office workspace with screens" style="background:linear-gradient(135deg,#dfe6ec,#7f8d9c)"></div>
      <h3>Digital Transformation</h3>
      <p>We guide change from strategy to implementation, improving systems, products and processes so your organisation is ready for a fast moving digital world.</p>
    </article>
  </section>

  <section class="what-we-do">
    <h2 class="section-title">What we do</h2>
    <p class="intro">We partner with leaders to build smarter digital businesses. Our approach blends sharp thinking, careful analysis and hands-on delivery, so plans become real results that last well beyond the first launch.</p>
    <div class="approach-row">
      <div class="approach">
        <div class="circle" role="img" aria-label="Abstract network of connected lights" style="background:radial-gradient(circle,#c9dcef,#3f6a96)"></div>
        <h3>Strategic Thinking</h3>
        <p>We look at the big picture, question assumptions and find the opportunities that will move your business forward.</p>
      </div>
      <div class="approach">
        <div class="circle" role="img" aria-label="Person studying data on a screen" style="background:radial-gradient(circle,#f2e3d6,#8c6d5a)"></div>
        <h3>Analytical Approach</h3>
        <p>Every recommendation is backed by data, research and insight, so you can make decisions with real confidence.</p>
      </div>
      <div class="approach">
        <div class="circle" role="img" aria-label="Team collaborating around a table" style="background:radial-gradient(circle,#e8e8e8,#6e6e6e)"></div>
        <h3>End to end project management</h3>
        <p>We stay with you from planning to launch, keeping projects on time, on budget and aligned to your goals.</p>
      </div>
    </div>
  </section>

  <section class="about">
    <div class="text">
      <h2 class="section-title">About us</h2>
      <p>Quillon Advisory was founded to give growing digital businesses access to senior strategic advice. We work with chief executives, managing directors and marketing leaders who want clear direction and practical support to grow.</p>
      <p>Our team combines experience across business strategy, marketing, digital products and campaigns. We keep things simple, focus on what matters and work closely with you to turn strategy into action, from first workshop to final delivery and beyond.</p>
    </div>
    <div class="about-img" role="img" aria-label="Glowing digital globe"></div>
  </section>

  <section class="director">
    <div class="director-photo" role="img" aria-label="Portrait of the director"></div>
    <div>
      <h2>Director Holly Prenwick</h2>
      <p>Holly Prenwick is a seasoned digital executive with broad experience in general management, strategy and marketing. She has worked across Australia and overseas in a range of industries, including e-commerce, media, travel and finance.</p>
      <p>With strength in people management, strategy and running digital businesses, Holly is results driven and passionate about growing businesses. She holds an MBA and a Bachelor of Business in Communication.</p>
      <p>Holly enjoys working with leaders who want to build something better. She brings energy, curiosity and a friendly, direct style to every engagement, helping teams move from ideas to delivery with confidence.</p>
    </div>
  </section>

  <footer class="site-footer">
    <div class="foot-col col-links">
      <h4>Quick links</h4>
      <ul><li>Home</li><li>Services</li><li>Careers</li><li>Investors</li><li>Media</li><li>Contact</li></ul>
    </div>
    <div class="foot-col col-services">
      <h4>Services</h4>
      <ul><li>Strategy</li><li>Marketing &amp; Campaigns</li><li>Digital Products</li><li>Social &amp; Search</li><li>Transformation</li></ul>
    </div>
    <div class="foot-col col-social">
      <h4>Follow Us</h4>
      <div class="socials"><span></span><span></span><span></span><span></span></div>
      <h4>Newsletter</h4>
      <div class="news-field"><span>Email Address</span><b>Subscribe</b></div>
    </div>
    <div class="foot-col">
      <h4>Contact Details</h4>
      <div class="contact-line">
        <svg width="16" height="20" viewBox="0 0 16 20"><path d="M8 0a7 7 0 0 0-7 7c0 5 7 13 7 13s7-8 7-13a7 7 0 0 0-7-7zm0 10a3 3 0 1 1 0-6 3 3 0 0 1 0 6z" fill="#e34197"/></svg>
        <div><strong>Quillon Advisory</strong><br>Strategy to implementation for<br>growing digital businesses.</div>
      </div>
      <div class="contact-line">
        <svg width="18" height="18" viewBox="0 0 18 18"><path d="M4 1l3 4-2 2c1 2 3 4 5 5l2-2 4 3-2 3C7 16 2 11 1 4z" fill="#e34197"/></svg>
        <span class="phone">123-555-0190</span>
      </div>
      <div class="contact-line">
        <svg width="18" height="14" viewBox="0 0 18 14"><rect x="0" y="0" width="18" height="14" rx="2" fill="#e34197"/><path d="M1 1l8 7 8-7" stroke="#2b2b2b" stroke-width="1.5" fill="none"/></svg>
        <span>info@quillonadvisory.com.au</span>
      </div>
    </div>
  </footer>
  <div class="bottom-bar">Copyright Quillon Advisory © 2016. All Rights Reserved</div>
</div>
</body>
</html>
```